Summit Bodyform Gym Website

We need a website design for our gym.

Summit is the UAE's first calisthenics and parkour gym. The theme under which the gym revolves is that one does not require any machinery to workout as our bodies could be themselves the machinery. The gym is designed to be the more of a social hub rather than an "in-and-out" gym, where people come train, have fun, hang out and socialize for a few hours rather than just train for 60 minutes then leave. The gym is designed to be a big open space with lots of natural sunlight, natural wood and plants all over the place to create a natural and refreshing setting. We also use recycled material throughout the gym and recycle our waste as being green is part of our philosophy. We currently also have some of the world's top and most recognized calisthenics athletes working with us.

We would like our website to reflect all that as well as provide a simple, interactive and fun way for visitors to be able to get class and gym information, check out gym media and contact us for bookings.

Target Market(s)

Ages 15-35

Industry/Entity Type

Fitness

Coding

Coded - Design and coding required

Number of Pages Required

4 page

Font styles to use
Decorative

Colors
0792cd

Requirements
Must have
• Class descriptions
• Gym description
• Class schedules
• Trainer profiles
• Gym philosophy
• Contact Details
Nice to have
• A link to contact us directly for a free first trial class

```html
<!DOCTYPE html>
<html lang="en">
<head>
<meta charset="utf-8">
<title>Summit Bodyform Gym</title>
<link rel="stylesheet" href="https://fonts.googleapis.com/css2?family=Open+Sans:wght@400;600&family=Roboto+Condensed:wght@400;700&display=swap">
<style>
:root{
  --brand:#0792cd;
  --brand-dark:#0a7fb0;
  --ink:#333;
  --muted:#666;
  --light:#e4e9eb;
  --dark:#1c1c1c;
  --dark-2:#262626;
  --white:#fff;
  --head-grey:#4a4a4a;
}
*{box-sizing:border-box;margin:0;padding:0}
html,body{width:1200px;height:2525px;overflow:hidden;background:var(--white)}
body{position:relative;font-family:"Open Sans",Arial,sans-serif;color:var(--ink)}
.abs{position:absolute}
.cond{font-family:"Roboto Condensed","Arial Narrow",sans-serif}

/* hero */
.hero{left:0;top:0;width:1200px;height:660px;background:linear-gradient(160deg,#2d3438 0%,#1f2a30 40%,#3a3f3a 70%,#1b2226 100%)}
.hero-slant{left:0;top:560px}
.brand{left:100px;top:50px;display:flex;align-items:center;gap:12px}
.brand-mark{width:22px;height:22px;border-radius:50%;background:var(--white)}
.brand-name{font-family:"Roboto Condensed",sans-serif;font-weight:700;font-size:48px;color:var(--white);letter-spacing:.5px}
.nav{left:429px;top:40px;display:flex;gap:30px;font-family:"Roboto Condensed",sans-serif;font-size:15px;color:var(--white);text-transform:uppercase}
.nav .active{color:var(--brand);border-bottom:2px solid var(--brand);padding-bottom:6px}
.hero-title{right:123px;top:258px;text-align:right;color:var(--white);font-family:"Roboto Condensed",sans-serif;font-weight:700}
.hero-title h1{font-size:52px;line-height:1;letter-spacing:.5px}
.hero-title p{font-size:25px;margin-top:8px}
.btn{display:inline-flex;align-items:center;justify-content:center;gap:14px;background:var(--brand);color:var(--white);font-family:"Roboto Condensed",sans-serif;text-transform:uppercase;border:2px solid rgba(255,255,255,.35);border-radius:3px}
.hero-btn{left:855px;top:370px;width:222px;height:42px;font-size:18px}
.arrow{top:310px}

/* section heads */
.sec-head{left:99px;display:flex;gap:16px;align-items:flex-start}
.sec-dot{width:14px;height:14px;border-radius:50%;background:var(--brand);margin-top:22px}
.sec-head h2{font-family:"Roboto Condensed",sans-serif;font-weight:400;font-size:31px;color:var(--head-grey);text-transform:uppercase;line-height:1.1}
.sec-head p{font-size:12px;color:var(--muted);margin-top:2px}

/* feature cards */
.card{top:757px;width:325px;height:350px;border:1px solid #9fd0e6;background:var(--white);box-shadow:0 2px 4px rgba(0,0,0,.12)}
.card-head{height:47px;background:var(--brand);color:var(--white);font-family:"Roboto Condensed",sans-serif;font-size:17px;text-transform:uppercase;display:flex;align-items:center;gap:10px;padding-left:22px}
.card-head.alt{background:var(--head-grey)}
.card-photo{height:182px}
.card-text{font-size:11.5px;line-height:1.75;color:var(--muted);text-align:center;padding:16px 22px 0}
.card-chev{position:absolute;left:50%;bottom:16px;transform:translateX(-50%)}

/* welcome band */
.welcome{left:0;top:1165px;width:1200px;height:500px}
.welcome-title{left:0;top:1325px;width:1200px;text-align:center;color:var(--white);font-family:"Roboto Condensed",sans-serif;font-size:38px;font-weight:400}
.welcome-text{left:210px;top:1388px;width:780px;text-align:center;color:var(--white);font-size:12px;line-height:1.75}
.welcome-btn{left:490px;top:1481px;width:220px;height:42px;font-size:16px;font-weight:700}

/* blog */
.post-photo{top:1823px;width:310px;height:157px;border:2px solid var(--brand)}
.post{top:2005px;width:310px}
.post-icon{position:absolute;left:0;top:0}
.post-line{position:absolute;left:20px;top:45px;width:1px;height:100px;background:#ddd}
.post-body{margin-left:66px}
.post-body h3{font-family:"Open Sans",sans-serif;font-weight:400;font-size:17px;color:var(--ink)}
.post-meta{font-size:10.5px;color:var(--muted);margin-top:6px;text-transform:uppercase}
.post-meta span{margin:0 8px}
.post-body p{font-size:11px;line-height:1.75;color:var(--muted);margin-top:6px}
.read-more{display:inline-block;margin-top:12px;font-size:12px;color:var(--brand);text-decoration:underline}

/* footer */
.footer{left:0;top:2183px;width:1200px;height:290px}
.foot-brand{left:118px;top:2222px;display:flex;align-items:center;gap:8px}
.foot-brand .brand-name{font-size:30px}
.foot-brand .brand-mark{width:14px;height:14px}
.contact{top:2235px;display:flex;gap:14px;align-items:center;color:var(--white);font-size:12px;line-height:1.6}
.contact strong{font-size:14px;font-weight:600}
.ring{width:34px;height:34px;border-radius:50%;border:1.5px solid var(--white);display:flex;align-items:center;justify-content:center;flex:none}
.foot-rule{left:118px;top:2311px;width:964px;height:1px;background:#444}
.news-title{left:118px;top:2338px;color:var(--white);font-size:15px;text-transform:uppercase}
.news-input{left:118px;top:2378px;width:328px;height:43px;border:1px solid #999;color:var(--white);font-size:11px;display:flex;align-items:center;justify-content:space-between;padding:0 14px}
.foot-links{left:582px;top:2356px;color:var(--white);font-size:11.5px;text-transform:uppercase}
.foot-links span{margin:0 6px}
.socials{left:582px;top:2390px;display:flex;gap:6px}
.socials i{width:24px;height:24px;border-radius:50%;border:1.5px solid var(--white);display:block}
.copy-bar{left:0;top:2466px;width:1200px;height:59px;background:var(--brand);color:var(--white);font-size:11px;display:flex;align-items:center;justify-content:center}
</style>
</head>
<body>

<!-- hero -->
<div class="abs hero" role="img" aria-label="Athlete performing a bar hold inside the gym with steel rigs and plants"></div>
<svg class="abs hero-slant" width="1200" height="100" viewBox="0 0 1200 100"><polygon points="0,22 1200,100 0,100" fill="#fff"/></svg>

<div class="abs brand"><span class="brand-name">Summit.</span><span class="brand-mark"></span></div>

<nav class="abs nav">
  <span class="active">Home</span><span>Class</span><span>Gym</span><span>Class Schedules</span><span>Trainer Profiles</span><span>Gym Philosophy</span><span>Contact</span>
</nav>

<svg class="abs arrow" style="left:48px" width="28" height="56" viewBox="0 0 28 56"><polyline points="26,2 2,28 26,54" fill="none" stroke="#fff" stroke-width="2" opacity=".7"/></svg>
<svg class="abs arrow" style="left:1128px" width="28" height="56" viewBox="0 0 28 56"><polyline points="2,2 26,28 2,54" fill="none" stroke="#fff" stroke-width="2" opacity=".7"/></svg>

<div class="abs hero-title">
  <h1>SUMMIT IS THE UAE'S</h1>
  <p>FIRST CALISTHENICS &amp; PARKOUR GYM</p>
</div>
<div class="abs btn hero-btn">Free First Trial Class</div>

<!-- intro -->
<div class="abs sec-head" style="top:655px">
  <span class="sec-dot"></span>
  <div><h2>Summit Bodyform Gym</h2><p>Lorem ipsum dolor sit amet, consectetur adipiscing</p></div>
</div>

<article class="abs card" style="left:99px">
  <div class="card-head"><svg width="16" height="16" viewBox="0 0 16 16"><rect x="1" y="3" width="14" height="12" fill="none" stroke="#fff" stroke-width="1.5"/><line x1="1" y1="7" x2="15" y2="7" stroke="#fff" stroke-width="1.5"/><line x1="5" y1="1" x2="5" y2="4" stroke="#fff" stroke-width="1.5"/><line x1="11" y1="1" x2="11" y2="4" stroke="#fff" stroke-width="1.5"/></svg>Class Schedules</div>
  <div class="card-photo" role="img" aria-label="Training floor with pull-up rigs and rings" style="background:linear-gradient(180deg,#cfd8dd,#7b8a92 70%,#4a555b)"></div>
  <p class="card-text">Lorem ipsum dolor sit amet, consectetur adipiscing elit, sed do eiusmod tempor incididunt ut labore et dolore magna aliqua. Ut enim ad</p>
  <svg class="card-chev" width="16" height="10" viewBox="0 0 16 10"><polyline points="1,1 8,8 15,1" fill="none" stroke="#555" stroke-width="2"/></svg>
</article>

<article class="abs card" style="left:441px">
  <div class="card-head alt"><svg width="26" height="12" viewBox="0 0 26 12"><rect x="0" y="2" width="3" height="8" fill="#fff"/><rect x="4" y="0" width="4" height="12" fill="#fff"/><rect x="8" y="5" width="10" height="2" fill="#fff"/><rect x="18" y="0" width="4" height="12" fill="#fff"/><rect x="23" y="2" width="3" height="8" fill="#fff"/></svg>Trainer Profiles</div>
  <div class="card-photo" role="img" aria-label="Two trainers posing with dumbbells" style="background:linear-gradient(135deg,#3d6078,#6b8fa3 50%,#2f4a5c)"></div>
  <p class="card-text">Lorem ipsum dolor sit amet, consectetur adipiscing elit, sed do eiusmod tempor incididunt ut labore et dolore magna aliqua. Ut enim ad</p>
  <svg class="card-chev" width="16" height="10" viewBox="0 0 16 10"><polyline points="1,1 8,8 15,1" fill="none" stroke="#555" stroke-width="2"/></svg>
</article>

<article class="abs card" style="left:784px">
  <div class="card-head"><svg width="16" height="16" viewBox="0 0 16 16"><rect x="1" y="3" width="14" height="12" fill="none" stroke="#fff" stroke-width="1.5"/><line x1="1" y1="7" x2="15" y2="7" stroke="#fff" stroke-width="1.5"/><line x1="5" y1="1" x2="5" y2="4" stroke="#fff" stroke-width="1.5"/><line x1="11" y1="1" x2="11" y2="4" stroke="#fff" stroke-width="1.5"/></svg>Gym Philosophy</div>
  <div class="card-photo" role="img" aria-label="Wooden wall with living plant lettering above a dumbbell rack" style="background:linear-gradient(180deg,#8a5a32,#6d4a2a 55%,#2a2a2a 80%,#5a2a22)"></div>
  <p class="card-text">Lorem ipsum dolor sit amet, consectetur adipiscing elit, sed do eiusmod tempor incididunt ut labore et dolore magna aliqua. Ut enim ad</p>
  <svg class="card-chev" width="16" height="10" viewBox="0 0 16 10"><polyline points="1,1 8,8 15,1" fill="none" stroke="#555" stroke-width="2"/></svg>
</article>

<!-- welcome band -->
<svg class="abs welcome" width="1200" height="500" viewBox="0 0 1200 500" role="img" aria-label="Wooden wall covered with green plant lettering and a row of dumbbells">
  <defs><linearGradient id="wood" x1="0" y1="0" x2="0" y2="1"><stop offset="0" stop-color="#6b4a30"/><stop offset=".5" stop-color="#4f3a26"/><stop offset=".85" stop-color="#2e2a22"/><stop offset="1" stop-color="#1e1e1e"/></linearGradient></defs>
  <polygon points="0,5 1200,50 1200,460 0,500" fill="url(#wood)"/>
  <polygon points="0,500 1200,460 1200,515 0,515" fill="#e4e9eb"/>
</svg>
<h2 class="abs welcome-title">WELCOME TO SUMMIT CALISTHENICS</h2>
<p class="abs welcome-text">Vestibulum commodo volutpat a, convallis ac, laoreet enim. Phasellus fermentum in, dolor pellentesque. Mulla imperdiet sit amet magna. Vestibulum dapibus. Vestibm commodo volutpat a, convallis ac, laoreet enim. Phasellus fermentum in, dolor pellentesque. Mulla imperdiet sit amet magna. Vetibulum dapibus. Vetibulum com volutpat a, convallis ac, laoreet enim. Phasellus fermentum in.</p>
<div class="abs btn welcome-btn">Get Started Today!
  <svg width="22" height="22" viewBox="0 0 22 22"><circle cx="11" cy="11" r="10" fill="none" stroke="#fff" stroke-width="1.2"/><polyline points="9,6 14,11 9,16" fill="none" stroke="#fff" stroke-width="1.5"/></svg>
</div>

<!-- blog -->
<div class="abs sec-head" style="top:1727px">
  <span class="sec-dot"></span>
  <div><h2>Summit Latest Blog</h2><p>Lorem ipsum dolor sit amet, consectetur adipiscing</p></div>
</div>

<div class="abs post-photo" style="left:99px" role="img" aria-label="Plant wall and dumbbell area" style="" ><div style="width:100%;height:100%;background:linear-gradient(180deg,#b07a45,#7a5535 60%,#7a2a22)"></div></div>
<div class="abs post-photo" style="left:444px" role="img" aria-label="Open training floor with pull-up rig"><div style="width:100%;height:100%;background:linear-gradient(180deg,#e8ecee,#9aa6ac 60%,#5c666b)"></div></div>
<div class="abs post-photo" style="left:789px" role="img" aria-label="Gymnastic ring hanging from a blue rig"><div style="width:100%;height:100%;background:linear-gradient(160deg,#d9e0e4,#3f7fb0 55%,#24323a)"></div></div>

<article class="abs post" style="left:99px">
  <svg class="post-icon" width="40" height="40" viewBox="0 0 40 40"><rect x="8" y="8" width="24" height="24" transform="rotate(45 20 20)" fill="#fff" stroke="#ddd"/><rect x="14" y="14" width="12" height="11" fill="none" stroke="#999" stroke-width="1.3"/><line x1="14" y1="18" x2="26" y2="18" stroke="#999" stroke-width="1.3"/></svg>
  <span class="post-line"></span>
  <div class="post-body">
    <h3>Lorem ipsum dolor sit amet,</h3>
    <div class="post-meta">Mar 21, 2013<span>\</span>2 comments</div>
    <p>Lorem ipsum dolor sit amet, consectetur adipiscing elit. Sed blandit massa vel mauris sollicitudin dignissim.</p>
    <span class="read-more">READ MORE</span>
  </div>
</article>
<article class="abs post" style="left:444px">
  <svg class="post-icon" width="40" height="40" viewBox="0 0 40 40"><rect x="8" y="8" width="24" height="24" transform="rotate(45 20 20)" fill="#fff" stroke="#ddd"/><rect x="14" y="14" width="12" height="11" fill="none" stroke="#999" stroke-width="1.3"/><line x1="14" y1="18" x2="26" y2="18" stroke="#999" stroke-width="1.3"/></svg>
  <span class="post-line"></span>
  <div class="post-body">
    <h3>Lorem ipsum dolor sit amet,</h3>
    <div class="post-meta">Mar 21, 2013<span>\</span>2 comments</div>
    <p>Lorem ipsum dolor sit amet, consectetur adipiscing elit. Sed blandit massa vel mauris sollicitudin dignissim.</p>
    <span class="read-more">READ MORE</span>
  </div>
</article>
<article class="abs post" style="left:789px">
  <svg class="post-icon" width="40" height="40" viewBox="0 0 40 40"><rect x="8" y="8" width="24" height="24" transform="rotate(45 20 20)" fill="#fff" stroke="#ddd"/><rect x="14" y="14" width="12" height="11" fill="none" stroke="#999" stroke-width="1.3"/><line x1="14" y1="18" x2="26" y2="18" stroke="#999" stroke-width="1.3"/></svg>
  <span class="post-line"></span>
  <div class="post-body">
    <h3>Lorem ipsum dolor sit amet,</h3>
    <div class="post-meta">Mar 21, 2013<span>\</span>2 comments</div>
    <p>Lorem ipsum dolor sit amet, consectetur adipiscing elit. Sed blandit massa vel mauris sollicitudin dignissim.</p>
    <span class="read-more">READ MORE</span>
  </div>
</article>

<!-- footer -->
<svg class="abs footer" width="1200" height="290" viewBox="0 0 1200 290" role="img" aria-label="Dark city skyline background">
  <defs><linearGradient id="foot" x1="0" y1="0" x2="0" y2="1"><stop offset="0" stop-color="#1a1a1a"/><stop offset="1" stop-color="#2a2a2a"/></linearGradient></defs>
  <polygon points="0,0 1200,22 1200,290 0,290" fill="url(#foot)"/>
</svg>

<div class="abs foot-brand"><span class="brand-name">Summit.</span><span class="brand-mark"></span></div>

<div class="abs contact" style="left:352px">
  <span class="ring"><svg width="12" height="16" viewBox="0 0 12 16"><path d="M6 1a5 5 0 0 1 5 5c0 4-5 9-5 9S1 10 1 6a5 5 0 0 1 5-5z" fill="none" stroke="#fff" stroke-width="1.4"/><circle cx="6" cy="6" r="1.8" fill="#fff"/></svg></span>
  <span>466 Summit (Cnr. Harlow &amp; Pen-<br>rose St.) Melbourne, VIC,</span>
</div>
<div class="abs contact" style="left:660px">
  <span class="ring"><svg width="14" height="14" viewBox="0 0 14 14"><path d="M3 1l2 3-1.5 1.5a8 8 0 0 0 5 5L10 9l3 2-1 2c-6 0-11-5-11-11z" fill="#fff"/></svg></span>
  <span>Phone :<br><strong>+1 1300 555 014</strong></span>
</div>
<div class="abs contact" style="left:900px">
  <span class="ring"><svg width="14" height="10" viewBox="0 0 14 10"><rect x=".7" y=".7" width="12.6" height="8.6" fill="none" stroke="#fff" stroke-width="1.3"/><polyline points="1,1 7,6 13,1" fill="none" stroke="#fff" stroke-width="1.3"/></svg></span>
  <span>E-mail:<br><strong>info@summitbodyform.example</strong></span>
</div>

<div class="abs foot-rule"></div>

<h4 class="abs news-title" style="font-weight:400">Newsletter Signup</h4>
<div class="abs news-input"><span>Enter your email address</span>
  <svg width="16" height="16" viewBox="0 0 16 16"><polygon points="1,7 15,1 10,15 8,9" fill="none" stroke="#fff" stroke-width="1.3"/></svg>
</div>

<div class="abs foot-links">Home<span>/</span>Class<span>/</span>Gym<span>/</span>Class Schedules<span>/</span>Trainer Profiles<span>/</span>Contact</div>
<div class="abs socials"><i></i><i></i><i></i><i></i><i></i></div>

<div class="abs copy-bar">©2014 - 2015 Summit calisthenics gym., All Rights Reserved.</div>

</body>
</html>
```